Bramblewood Joinery Website

My client Bramblewood Joinery is looking for a redesign for a Word Press Website. Their current site is at www.bramblewoodjoinery.example They are a custom cabinet company, but also create bathroom, living room, bar and entertainment and bedroom cabinets too. They would like a design that emulates the master craftsman work they do yet a contemporary style.

Their current site was designed using Flash elements.

Target Market(s)

Home owners and builders of high end homes

Industry/Entity Type

Entertainment

Font styles to use
Serif
Decorative

Requirements
Must have
• Must show their work and logo using a contemporary style.
Nice to have
• Sliders that showcase their projects.

```html
<!DOCTYPE html>
<html lang="en">
<head>
<meta charset="utf-8">
<title>Bramblewood Joinery</title>
<link href="https://fonts.googleapis.com/css2?family=Cinzel:wght@400&family=Vollkorn:ital,wght@0,400;0,500;1,400&family=Open+Sans:wght@400;600&family=PT+Sans:wght@400&display=swap" rel="stylesheet">
<style>
:root{
  --green:#2fa836;
  --green-dark:#238a29;
  --ink:#222;
  --text:#555;
  --muted:#777;
  --dark:#242424;
  --line:#e3e3e3;
  --white:#fff;
}
*{margin:0;padding:0;box-sizing:border-box}
html,body{width:1200px;height:2761px;overflow:hidden;background:var(--white)}
body{font-family:"PT Sans",sans-serif;color:var(--text);position:relative}
.abs{position:absolute}
.green{color:var(--green)}

.site-header{left:0;top:0;width:1200px;height:98px;background:var(--white)}
.brand{left:88px;top:10px;display:flex;align-items:center;gap:10px}
.brand-mark{width:22px;height:22px;border-radius:50%;background:var(--green)}
.brand-name{font-family:"Vollkorn",serif;font-size:22px;color:var(--ink)}
.contact{right:172px;top:30px;text-align:right;font-family:"Open Sans",sans-serif}
.contact .ask{font-size:14px;color:var(--green)}
.contact .phone{font-size:14px;color:#888;margin-top:4px}
.search{left:1070px;top:32px;width:44px;height:38px;background:#eee;border-radius:3px}

.dark-band{left:0;top:98px;width:1200px;height:522px;background:var(--dark)}
.main-nav{left:88px;top:128px;width:1024px;height:62px;background:var(--white);border-radius:3px;display:flex;align-items:center;justify-content:space-between;padding:0 35px;font-family:"Open Sans",sans-serif;font-weight:600;font-size:14.5px;color:var(--ink)}
.main-nav .current{color:var(--green)}

.hero{left:88px;top:222px;width:1024px;height:493px}
.hero-photo{position:absolute;inset:0}
.hero-text{position:absolute;left:0;top:150px;width:100%;text-align:center;color:var(--white);font-family:"Cinzel",serif}
.hero-text .line1{font-family:"Vollkorn",serif;font-size:60px;line-height:1}
.hero-text .line2{font-size:74px;line-height:1.2;margin-top:10px;letter-spacing:1px}
.hero-text .cta{font-size:29px;margin-top:22px;display:inline-flex;align-items:center;gap:22px;letter-spacing:1px}
.dots{position:absolute;left:492px;top:455px;display:flex;gap:8px}
.dots span{width:8px;height:8px;border-radius:50%;background:#ddd}
.dots span.on{background:var(--green)}

.section-title{left:0;width:1200px;text-align:center;font-family:"Vollkorn",serif;font-size:29px;color:var(--ink)}
.intro{left:120px;top:792px;width:960px;text-align:center;font-size:13.5px;line-height:21px}

.card{left:88px;width:1024px;height:256px;background:var(--white);box-shadow:0 1px 7px rgba(0,0,0,.22)}
.card .photo{position:absolute;top:20px;width:490px;height:216px;border:5px solid #e8e8e8}
.card .body{position:absolute;top:24px;width:437px}
.card h3{font-family:"Open Sans",sans-serif;font-weight:400;font-size:21px;color:var(--ink);margin-bottom:16px}
.card ul{list-style:none}
.card li{font-size:12px;display:flex;align-items:center;gap:12px;margin-bottom:12px}
.card p{font-size:12px;line-height:18px;margin-top:18px}
.btn{display:inline-block;margin-top:30px;background:var(--green);color:var(--white);font-family:"Open Sans",sans-serif;font-size:15px;padding:8px 22px;border-radius:2px}

.pager{right:88px;top:1834px;display:flex;gap:9px;font-size:12px}
.pager span{background:#ddd;color:#999;height:24px;line-height:24px;padding:0 9px}
.pager .wide{width:76px;text-align:center}
.pager .on{background:var(--green);color:var(--white)}

.latest-intro{left:88px;top:1940px;width:302px}
.latest-intro h4{font-family:"Open Sans",sans-serif;font-weight:400;font-size:18px;color:var(--ink);margin-bottom:12px}
.latest-intro p{font-size:12.5px;line-height:19px;margin-bottom:18px}
.latest-intro hr{border:0;border-top:1px solid var(--line);margin-top:16px}
.slider-ctrl{left:88px;top:2122px;width:300px;height:34px}
.round{position:absolute;top:0;width:34px;height:34px;border-radius:50%;border:1px solid #ccc}
.mini-dots{position:absolute;left:118px;top:15px;display:flex;gap:26px}
.mini-dots span{width:4px;height:4px;border-radius:50%;background:#999}
.work{top:1946px;width:215px;height:212px;background:#f4f4f4;box-shadow:0 1px 3px rgba(0,0,0,.12);text-align:center}
.work .photo{height:142px}
.work h5{font-family:"Open Sans",sans-serif;font-weight:400;font-size:15px;color:var(--green);margin-top:14px}
.work p{font-size:11.5px;color:var(--muted);margin-top:5px}

.testimonial{top:2270px;width:400px;text-align:center}
.avatar{width:140px;height:140px;border-radius:50%;border:4px solid #eee;margin:0 auto;background:linear-gradient(#d9d9d9,#9a9a9a)}
.quote-mark{font-family:"Vollkorn",serif;font-size:52px;color:#ccc;line-height:1;margin-top:18px;height:40px}
.testimonial blockquote{font-family:"Vollkorn",serif;font-style:italic;font-size:13.5px;line-height:24px;color:var(--muted);margin-top:6px}
.testimonial cite{display:block;font-style:normal;font-family:"Open Sans",sans-serif;font-size:16px;color:var(--green);margin-top:16px}

.site-footer{left:0;top:2614px;width:1200px;height:147px;background:var(--dark);text-align:center}
.foot-nav{margin-top:26px;display:flex;justify-content:center;gap:22px;font-size:12px;color:var(--green)}
.copyright{font-size:11px;color:#ccc;margin-top:10px}
.social{display:flex;justify-content:center;gap:14px;margin-top:20px}
.social span{width:34px;height:34px;border-radius:3px}
</style>
</head>
<body>

<header class="site-header abs">
  <div class="brand abs" style="top:38px">
    <span class="brand-mark"></span>
    <span class="brand-name">Bramblewood Joinery</span>
  </div>
  <div class="contact abs">
    <div class="ask">Have a Question for Us ?</div>
    <div class="phone">555.014.2300</div>
  </div>
  <div class="search abs">
    <svg width="44" height="38" viewBox="0 0 44 38"><circle cx="20" cy="17" r="7" fill="none" stroke="#bbb" stroke-width="2"/><line x1="25" y1="22" x2="31" y2="28" stroke="#bbb" stroke-width="2.5"/></svg>
  </div>
</header>

<div class="dark-band abs"></div>

<nav class="main-nav abs">
  <span class="current">Home</span><span>Who We Are</span><span>Getting Started</span><span>Customer Experience</span><span>Professional</span><span>Portfolio</span><span>Cabinet Hardware</span><span>Contact Us</span>
</nav>

<section class="hero abs">
  <svg class="hero-photo" width="1024" height="493" viewBox="0 0 1024 493" role="img" aria-label="Modern kitchen interior with dark wood island and large windows">
    <defs>
      <linearGradient id="heroTone" x1="0" y1="0" x2="1" y2="1">
        <stop offset="0" stop-color="#7d7670"/>
        <stop offset=".5" stop-color="#5a4a40"/>
        <stop offset="1" stop-color="#3a2520"/>
      </linearGradient>
    </defs>
    <path d="M0 0H1024V450Q512 530 0 450Z" fill="url(#heroTone)"/>
    <path d="M0 450Q512 530 0 450Z" fill="none"/>
  </svg>
  <div class="hero-text">
    <div class="line1">The Definition of</div>
    <div class="line2">Above and Beyond</div>
    <div class="cta">Start Now
      <svg width="28" height="16" viewBox="0 0 28 16"><path d="M0 8H24M17 1L25 8L17 15" fill="none" stroke="#fff" stroke-width="3"/></svg>
    </div>
  </div>
  <div class="dots"><span class="on"></span><span></span><span></span></div>
</section>

<h2 class="section-title abs" style="top:748px">Who <span class="green">We Are</span></h2>
<p class="intro abs">Temporibus autem quibusdam et aut officiis debitis aut rerum necessitatibus saepe evenietNeque porro quisquam est, qui dolorem ipsum quia dolor sit amet, consectetur, adipisci velit, sed quia non numquam eius modi tempora incidunt ut labore et dolore magnam aliquam quaerat voluptatem.Ut enim ad minima veniam, quis nostrum exercitationem ullam corporis suscipit laboriosam, nisi ut aliquid ex ea commodi consequatur.</p>

<h2 class="section-title abs" style="top:880px">Our <span class="green">Portfolio</span></h2>

<article class="card abs" style="top:940px">
  <div class="photo" style="left:20px;background:linear-gradient(135deg,#d9d6d0,#7a7670 60%,#2c2a28)" role="img" aria-label="White custom kitchen cabinets with dark island"></div>
  <div class="body" style="left:567px">
    <h3>Kitchens</h3>
    <ul>
      <li><svg width="14" height="12" viewBox="0 0 14 12"><path d="M1 6L5 10L13 1" fill="none" stroke="#2fa836" stroke-width="2.5"/></svg>Etiam interdum eros sit amet nunc egestas, at scelerisque lacus molestie.</li>
      <li><svg width="14" height="12" viewBox="0 0 14 12"><path d="M1 6L5 10L13 1" fill="none" stroke="#2fa836" stroke-width="2.5"/></svg>Etiam interdum eros sit amet nunc egestas, at scelerisque lacus molestie.</li>
    </ul>
    <p>Voluptate illum dolore Voluptate illum dolore ita ipsum, quid deserunt singulis, labore admodum ita multos malis ea nam nam tamen fore amet. Vidisse quid doctrina.</p>
    <span class="btn">Know More</span>
  </div>
</article>

<article class="card abs" style="top:1248px">
  <div class="body" style="left:22px">
    <h3>Office</h3>
    <ul>
      <li><svg width="14" height="12" viewBox="0 0 14 12"><path d="M1 6L5 10L13 1" fill="none" stroke="#2fa836" stroke-width="2.5"/></svg>Etiam interdum eros sit amet nunc egestas, at scelerisque lacus molestie.</li>
      <li><svg width="14" height="12" viewBox="0 0 14 12"><path d="M1 6L5 10L13 1" fill="none" stroke="#2fa836" stroke-width="2.5"/></svg>Etiam interdum eros sit amet nunc egestas, at scelerisque lacus molestie.</li>
    </ul>
    <p>Voluptate illum dolore Voluptate illum dolore ita ipsum, quid deserunt singulis, labore admodum ita multos malis ea nam nam tamen fore amet. Vidisse quid doctrina.</p>
    <span class="btn">Know More</span>
  </div>
  <div class="photo" style="left:514px;background:linear-gradient(135deg,#6a3320,#4a2418 55%,#2a140e)" role="img" aria-label="Home office with built-in wooden bookshelves"></div>
</article>

<article class="card abs" style="top:1553px">
  <div class="photo" style="left:20px;background:linear-gradient(135deg,#dfe8b0,#b9d66a 50%,#f2f2ea)" role="img" aria-label="Bright living room with green sofas and wall units"></div>
  <div class="body" style="left:567px">
    <h3>living room</h3>
    <ul>
      <li><svg width="14" height="12" viewBox="0 0 14 12"><path d="M1 6L5 10L13 1" fill="none" stroke="#2fa836" stroke-width="2.5"/></svg>Etiam interdum eros sit amet nunc egestas, at scelerisque lacus molestie.</li>
      <li><svg width="14" height="12" viewBox="0 0 14 12"><path d="M1 6L5 10L13 1" fill="none" stroke="#2fa836" stroke-width="2.5"/></svg>Etiam interdum eros sit amet nunc egestas, at scelerisque lacus molestie.</li>
    </ul>
    <p>Voluptate illum dolore Voluptate illum dolore ita ipsum, quid deserunt singulis, labore admodum ita multos malis ea nam nam tamen fore amet. Vidisse quid doctrina.</p>
    <span class="btn">Know More</span>
  </div>
</article>

<div class="pager abs"><span class="wide">Previous</span><span class="on">1</span><span>2</span><span>3</span><span>4</span><span class="wide">Next</span></div>

<h2 class="section-title abs" style="top:1884px">Our <span class="green">Latest work</span></h2>

<div class="latest-intro abs">
  <h4>Reprehenderit voluptate velit esse</h4>
  <p>Temporibus autem quibusdam et aut officiis debitis aut rerum necessitatibus saepe eveniet Nam libero tempore, cum soluta nobis est eligendi optio.</p>
  <p>Quis autem vel eum iure reprehenderit qui in.</p>
  <hr>
</div>
<div class="slider-ctrl abs">
  <span class="round" style="left:0"><svg width="32" height="32" viewBox="0 0 32 32"><path d="M18 11L13 16L18 21" fill="none" stroke="#888" stroke-width="1.6"/></svg></span>
  <div class="mini-dots"><span></span><span></span><span></span></div>
  <span class="round" style="left:264px"><svg width="32" height="32" viewBox="0 0 32 32"><path d="M14 11L19 16L14 21" fill="none" stroke="#888" stroke-width="1.6"/></svg></span>
</div>

<div class="work abs" style="left:430px">
  <div class="photo" style="background:linear-gradient(135deg,#3a2a22,#c9c3b8 60%,#e6e2da)" role="img" aria-label="Kitchen project with white cabinets"></div>
  <h5>Voluptate Velit Esse</h5><p>At vero accusamus et iusto odio[..]</p>
</div>
<div class="work abs" style="left:663px">
  <div class="photo" style="background:linear-gradient(135deg,#4a3a30,#d4cec4 55%,#efece6)" role="img" aria-label="Kitchen project with glass-front cabinets"></div>
  <h5>Voluptate Velit Esse</h5><p>At vero accusamus et iusto odio[..]</p>
</div>
<div class="work abs" style="left:897px">
  <div class="photo" style="background:linear-gradient(135deg,#6b4a34,#2a2624 55%,#4a3426)" role="img" aria-label="Dark wood kitchen island project"></div>
  <h5>Voluptate Velit Esse</h5><p>At vero accusamus et iusto odio[..]</p>
</div>

<h2 class="section-title abs" style="top:2204px">Customer <span class="green">Experience</span></h2>

<div class="testimonial abs" style="left:142px">
  <div class="avatar" role="img" aria-label="Portrait of the builder"></div>
  <div class="quote-mark">&ldquo;</div>
  <blockquote>Suspendisse dictum feugiat nisl ut dapibus. Mauris iaculis porttitor posuere. Praesent id.Suspendisse dictum feugiat nisl ut dapibus. Mauris iaculis porttitor posuere. Praesent id.</blockquote>
  <cite>- Builder, Dan Hollis</cite>
</div>
<div class="testimonial abs" style="left:654px">
  <div class="avatar" role="img" aria-label="Portrait of the homeowner"></div>
  <div class="quote-mark">&ldquo;</div>
  <blockquote>Suspendisse dictum feugiat nisl ut dapibus. Mauris iaculis porttitor posuere. Praesent id.Suspendisse dictum feugiat nisl ut dapibus. Mauris iaculis porttitor posuere. Praesent id.</blockquote>
  <cite>- Homeowner, Martin P.</cite>
</div>

<footer class="site-footer abs">
  <nav class="foot-nav"><span>Home</span><span>Who We Are</span><span>Getting Started</span><span>Customer Experience</span><span>Professional</span><span>Portfolio</span><span>Cabinet Hardware</span><span>Contact Us</span></nav>
  <div class="copyright">Copyright © 2015 BramblewoodJoinery.All Rights Reserved</div>
  <div class="social">
    <span style="background:#3b5ea8"></span><span style="background:#2d9fd9"></span><span style="background:#1c6fa8"></span><span style="background:#c9302c"></span>
  </div>
</footer>

</body>
</html>
```